Bork Ventures, Inc. Website redesign

Revamp the website, it is old and outdated. www.borkventuresinc.example

Target Market(s)

Information Technology Consulting and Staffing

Coding

Coded - Design and coding required

Number of Pages Required

5+ page

Colors

Designer to choose colors to be used in the design.

Requirements
Must have
• Outlined text boxes just like from the Tolvane.example site. A clean look

```html
<!DOCTYPE html>
<html lang="en">
<head>
<meta charset="utf-8">
<title>Bork Ventures, Inc.</title>
<link href="https://fonts.googleapis.com/css2?family=Dosis:wght@400;500;600;700&family=Montserrat:wght@500;600&display=swap" rel="stylesheet">
<style>
:root{
  --brand:#8c0d26;
  --ink:#1c1c1c;
  --text:#555;
  --muted:#777;
  --paper:#fff;
  --mist:#f3f3f3;
  --line:#dcdcdc;
  --footer:#262626;
  --hero-a:#22344a;
  --hero-b:#3c5f7d;
}
*{box-sizing:border-box;margin:0;padding:0}
html,body{width:1200px;height:2829px;overflow:hidden}
body{position:relative;background:var(--paper);font-family:Arial,Helvetica,sans-serif;color:var(--text)}

/* header */
.site-header{position:absolute;left:0;top:0;width:1200px;height:115px}
.brand-name{position:absolute;left:110px;top:38px;width:230px;white-space:nowrap;font-family:"Dosis",sans-serif;font-weight:700;font-size:26px;letter-spacing:.5px;color:var(--ink);display:flex;align-items:center;gap:10px;line-height:1}
.brand-name .mark{width:22px;height:22px;background:var(--brand);flex:none}
.motto{position:absolute;left:360px;top:40px;white-space:nowrap;font-family:"Dosis",sans-serif;font-variant:small-caps;font-size:28px;font-weight:400;color:#444;letter-spacing:.5px;line-height:1.1}
.call{position:absolute;left:819px;top:30px;display:flex;align-items:center;gap:11px;white-space:nowrap}
.call .dot{width:52px;height:52px;border-radius:50%;background:var(--brand);display:flex;align-items:center;justify-content:center}
.call span{font-family:"Dosis",sans-serif;font-weight:700;font-size:21px;color:var(--ink)}

/* nav */
.main-nav{position:absolute;left:0;top:116px;width:1200px;height:61px;background:var(--brand);border-bottom:4px solid #fff;box-sizing:content-box}
.main-nav ul{list-style:none;position:absolute;left:110px;top:0;display:flex;height:61px;align-items:center}
.main-nav li{font-family:"Montserrat",sans-serif;font-weight:500;font-size:13px;color:#fff;height:61px;display:flex;align-items:center;justify-content:center;position:relative;white-space:nowrap}
.main-nav li.active{background:#0c0c0c;width:162px}
.main-nav li + li::before{content:"";position:absolute;left:0;top:24px;height:14px;border-left:1px solid rgba(255,255,255,.7)}
.main-nav li.active + li::before{display:none}

/* hero */
.hero{position:absolute;left:0;top:181px;width:1200px;height:737px;background:radial-gradient(ellipse at 50% 55%,var(--hero-b) 0%,var(--hero-a) 70%,#1a2535 100%)}
.hero-title{position:absolute;left:0;width:1200px;top:240px;text-align:center;font-family:"Dosis",sans-serif;font-weight:600;font-size:78px;color:#fff;letter-spacing:2px;line-height:1.1}
.hero-sub{position:absolute;left:0;width:1200px;top:344px;text-align:center;font-family:"Dosis",sans-serif;font-weight:600;font-size:22px;color:#fff}
.hero-btn{position:absolute;left:510px;top:415px;width:180px;height:56px;border:2px solid #fff;border-radius:28px;background:var(--brand);color:#fff;font-family:"Dosis",sans-serif;font-weight:600;font-size:21px;display:flex;align-items:center;justify-content:center}
.hero-arrow{position:absolute;top:329px;width:35px;height:35px;border:2px solid #fff;border-radius:50%;display:flex;align-items:center;justify-content:center}

.services-band{position:absolute;left:0;top:918px;width:1200px;height:410px;background:var(--mist)}
.service-card{position:absolute;top:812px;width:309px;height:450px;background:#fff;border-top:4px solid var(--brand);box-shadow:0 1px 3px rgba(0,0,0,.15)}
.service-card h3{position:absolute;left:20px;top:34px;font-family:"Dosis",sans-serif;font-weight:600;font-size:16px;color:var(--ink);letter-spacing:.3px;white-space:nowrap}
.service-card .photo{position:absolute;left:0;top:83px;width:309px;height:179px}
.service-card p{position:absolute;left:19px;top:287px;width:274px;font-size:12.5px;line-height:27.5px;text-align:justify;color:var(--text)}
.service-card .more{position:absolute;left:20px;top:385px;width:115px;height:37px;background:var(--brand);color:#fff;font-size:13px;display:flex;align-items:center;justify-content:center}

/* strategy */
.section-title{position:absolute;left:0;width:1200px;text-align:center;font-family:"Dosis",sans-serif;font-weight:600;font-size:40px;color:var(--ink)}
.section-title em{font-style:normal;color:var(--brand)}
.step{position:absolute;top:1476px;width:235px;height:324px;border:1px solid var(--line);border-bottom:3px solid var(--brand);text-align:center}
.step svg{position:absolute;left:48px;top:13px}
.step h4{position:absolute;left:0;width:100%;top:190px;font-family:"Dosis",sans-serif;font-weight:600;font-size:19px;color:var(--ink)}
.step p{position:absolute;left:8px;width:217px;top:227px;font-size:13px;line-height:25.6px;color:var(--muted)}

/* leaders */
.leaders-band{position:absolute;left:0;top:1873px;width:1200px;height:574px;background:var(--mist)}
.leaders-intro{position:absolute;left:0;width:1200px;top:1979px;text-align:center;font-size:12.5px;color:#333}
.leader{position:absolute;top:2036px;width:468px;height:299px;background:#fff;border:1px solid var(--line);border-top:4px solid var(--brand)}
.leader .portrait{position:absolute;left:19px;top:40px;width:150px;height:150px;border-radius:50%}
.leader h5{position:absolute;left:205px;top:42px;font-family:"Dosis",sans-serif;font-weight:600;font-size:16px;color:var(--brand);white-space:nowrap}
.leader p{position:absolute;left:204px;top:79px;width:235px;font-size:12.5px;line-height:25.6px;text-align:justify;color:#444}
.pager{position:absolute;top:2374px;width:12px;height:12px;border-radius:50%;background:#555}

/* footer */
.site-footer{position:absolute;left:0;top:2447px;width:1200px;height:382px;background:var(--footer);color:#fff}
.footer-brand{position:absolute;left:0;width:1200px;top:50px;display:flex;justify-content:center;align-items:center;gap:14px;font-family:"Dosis",sans-serif;font-weight:700;font-size:44px;letter-spacing:1px;color:#fff;line-height:1}
.footer-brand .mark{width:32px;height:32px;background:#fff}
.contact-line{position:absolute;left:0;width:1200px;top:148px;display:flex;justify-content:center;gap:28px;font-size:13.5px;align-items:center}
.contact-line span{display:flex;align-items:center;gap:7px}
.footer-nav{position:absolute;left:0;width:1200px;top:202px;text-align:center;font-size:13.5px;word-spacing:2px}
.footer-nav i{font-style:normal;margin:0 22px}
.socials{position:absolute;left:496px;top:259px;display:flex;gap:7px}
.socials span{width:36px;height:36px;border:1.5px solid #fff;border-radius:50%}
.copyright{position:absolute;left:0;width:1200px;top:321px;text-align:center;font-size:13.5px;color:#ddd}
</style>
</head>
<body>

<header class="site-header">
  <div class="brand-name"><span class="mark"></span>BORK VENTURES</div>
  <div class="motto">Mission Integrity Results</div>
  <div class="call">
    <div class="dot"><svg width="18" height="18" viewBox="0 0 24 24"><path fill="#fff" d="M6.6 10.8a15 15 0 0 0 6.6 6.6l2.2-2.2c.3-.3.7-.4 1-.2 1.1.4 2.3.6 3.6.6.6 0 1 .4 1 1V20c0 .6-.4 1-1 1A17 17 0 0 1 3 4c0-.6.4-1 1-1h3.5c.6 0 1 .4 1 1 0 1.3.2 2.5.6 3.6.1.3 0 .7-.2 1z"/></svg></div>
    <span>CALL US : 555-010-2468</span>
  </div>
</header>

<nav class="main-nav">
  <ul>
    <li class="active">HOME</li>
    <li style="width:152px">ABOUT US</li>
    <li style="width:156px">SERVICES</li>
    <li style="width:163px">STRATEGY</li>
    <li style="width:146px">IT NEWS</li>
    <li style="width:179px">CONTACT US</li>
  </ul>
</nav>

<section class="hero" role="img" aria-label="Businessman holding glowing network of devices, servers and a security lock in his palm">
  <div class="hero-title">BORK VENTURES</div>
  <div class="hero-sub">BRINGING THOUGHT LEADERSHIP AND QUALITY TO EVERY PROJECT</div>
  <div class="hero-btn">GET STARTED</div>
  <div class="hero-arrow" style="left:68px"><svg width="12" height="12" viewBox="0 0 12 12"><path d="M8 1L3 6l5 5" stroke="#fff" stroke-width="2" fill="none"/></svg></div>
  <div class="hero-arrow" style="left:1097px"><svg width="12" height="12" viewBox="0 0 12 12"><path d="M4 1l5 5-5 5" stroke="#fff" stroke-width="2" fill="none"/></svg></div>
</section>

<div class="services-band"></div>

<article class="service-card" style="left:111px">
  <h3>HARDWARE / SOFTWARE SALES</h3>
  <div class="photo" role="img" aria-label="Consultant explaining a network diagram on a whiteboard to colleagues" style="background:linear-gradient(135deg,#d9d4c8,#f1efe9 60%,#b9b2a4)"></div>
  <p>We have access to multiple distributor partners throughout North America, as well as Partner many of the industry's manufacturers</p>
  <div class="more">LEARN MORE</div>
</article>
<article class="service-card" style="left:445px">
  <h3>PROFESSIONAL SERVICES</h3>
  <div class="photo" role="img" aria-label="Two engineers working in a server room" style="background:linear-gradient(135deg,#3a3d42,#8a8f96 50%,#2b2d31)"></div>
  <p>Our team provides experienced leadership and guidance, utilizing the industry standard &nbsp;We maintain acomprehe nsive view of strategy</p>
  <div class="more">LEARN MORE</div>
</article>
<article class="service-card" style="left:780px">
  <h3>TECHNOLOGY ASSESSMENT</h3>
  <div class="photo" role="img" aria-label="Technician inspecting cabling in a server rack" style="background:linear-gradient(135deg,#c9cbcd,#55585c 55%,#1f2124)"></div>
  <p>Experience has shown companies that perform objective, third-party technology assessments instrumental in identifying weaknesses</p>
  <div class="more">LEARN MORE</div>
</article>

<h2 class="section-title" style="top:1385px">OUR <em>STRATEGY</em></h2>

<div class="step" style="left:111px">
  <svg width="137" height="157" viewBox="0 0 137 157"><polygon points="68.5,2 134.5,40 134.5,117 68.5,155 2.5,117 2.5,40" fill="none" stroke="#8c0d26" stroke-width="2"/><rect x="52" y="46" width="40" height="62" fill="none" stroke="#8c0d26" stroke-width="3"/><path d="M60 58h24M60 66h24M60 74h24" stroke="#8c0d26" stroke-width="2.5"/><circle cx="50" cy="95" r="14" fill="#fff" stroke="#8c0d26" stroke-width="3"/><path d="M43 95l5 5 9-10" stroke="#8c0d26" stroke-width="3" fill="none"/></svg>
  <h4>ASSESS</h4>
  <p>Our case-specific technology audit and data gathering provides us with a detailed &amp; comprehensive</p>
</div>
<div class="step" style="left:359px">
  <svg width="137" height="157" viewBox="0 0 137 157"><polygon points="68.5,2 134.5,40 134.5,117 68.5,155 2.5,117 2.5,40" fill="none" stroke="#8c0d26" stroke-width="2"/><rect x="36" y="78" width="12" height="30" fill="none" stroke="#8c0d26" stroke-width="3"/><path d="M52 80l10-18c3-5 9-3 8 3l-3 11h18c5 0 6 6 2 8 4 1 4 7 0 8 3 2 2 7-2 8 2 3 0 7-4 7H52z" fill="none" stroke="#8c0d26" stroke-width="3" stroke-linejoin="round"/><path d="M66 38v10M52 44l5 7M80 44l-5 7" stroke="#8c0d26" stroke-width="3"/></svg>
  <h4>RECOMMEND</h4>
  <p>Our research and analysis is summarized in a proposal for indivi dually designed solutions</p>
</div>
<div class="step" style="left:606px">
  <svg width="137" height="157" viewBox="0 0 137 157"><polygon points="68.5,2 134.5,40 134.5,117 68.5,155 2.5,117 2.5,40" fill="none" stroke="#8c0d26" stroke-width="2"/><circle cx="68" cy="78" r="14" fill="none" stroke="#8c0d26" stroke-width="3"/><circle cx="68" cy="78" r="5" fill="none" stroke="#8c0d26" stroke-width="3"/><path d="M68 58v6M68 92v6M48 78h6M82 78h6M54 64l4 4M78 88l4 4M54 92l4-4M78 68l4-4" stroke="#8c0d26" stroke-width="3"/><path d="M30 104h20l14 6h22M106 52H86l-14-6H52" stroke="#8c0d26" stroke-width="3" fill="none"/></svg>
  <h4>IMPLEMENT</h4>
  <p>Bork Ventures, Inc. manages all aspects of the implementation process, including design</p>
</div>
<div class="step" style="left:854px">
  <svg width="137" height="157" viewBox="0 0 137 157"><polygon points="68.5,2 134.5,40 134.5,117 68.5,155 2.5,117 2.5,40" fill="none" stroke="#8c0d26" stroke-width="2"/><rect x="30" y="54" width="56" height="38" fill="none" stroke="#8c0d26" stroke-width="3"/><path d="M30 84h56M52 92v8M44 100h28" stroke="#8c0d26" stroke-width="3"/><rect x="78" y="66" width="18" height="34" fill="#fff" stroke="#8c0d26" stroke-width="3"/><rect x="92" y="74" width="14" height="26" fill="#fff" stroke="#8c0d26" stroke-width="3"/></svg>
  <h4>MONITOR</h4>
  <p>Ensuring that your technology performs optimally and securely at all times is our job.</p>
</div>

<div class="leaders-band"></div>
<h2 class="section-title" style="top:1915px">OUR <em>LEADERS</em></h2>
<p class="leaders-intro">We provide our clients with cutting-edge technologies and the know-how to apply them to their individual</p>

<article class="leader" style="left:111px">
  <div class="portrait" role="img" aria-label="Black and white portrait of the co-founder" style="background:radial-gradient(circle at 50% 40%,#bdbdbd,#555 75%,#222)"></div>
  <h5>RAVIN DASHAL- CO-FOUNDER</h5>
  <p>Ravin has played a leading role in the global information technology industry for more than 20 years, managing divisions and business the United States. Since founding Bork Ventures, Inc. (BVI) in 2008, he has been instrumental in formulating the company's strategy</p>
</article>
<article class="leader" style="left:620px">
  <div class="portrait" role="img" aria-label="Black and white portrait of the chief technology officer" style="background:radial-gradient(circle at 50% 40%,#9a9a9a,#3a3a3a 70%,#e8e8e8)"></div>
  <h5 style="top:38px">DELMAR VANCE - CHIEF TECHNOLOGY</h5>
  <p style="top:75px">Delmar Vance is the Chief Technology Officer for Bork Ventures, INC. Mr. Vance, an eighteen-year veteran in the IT industry, is responsible for developing the overall technology vision for the company, driving cross-company engineering initiatives and collaboration, and overseeing</p>
</article>

<span class="pager" style="left:577px"></span>
<span class="pager" style="left:594px;background:var(--brand)"></span>
<span class="pager" style="left:612px"></span>

<footer class="site-footer">
  <div class="footer-brand"><span class="mark"></span>BORK VENTURES</div>
  <div class="contact-line">
    <span><svg width="10" height="14" viewBox="0 0 10 14"><path d="M5 0a5 5 0 0 0-5 5c0 4 5 9 5 9s5-5 5-9a5 5 0 0 0-5-5zm0 7a2 2 0 1 1 0-4 2 2 0 0 1 0 4z" fill="#8c0d26"/></svg>2200 Harlow Lane, Fairbrook, MD 20999</span>
    <span><svg width="13" height="13" viewBox="0 0 24 24"><path fill="#8c0d26" d="M6.6 10.8a15 15 0 0 0 6.6 6.6l2.2-2.2c.3-.3.7-.4 1-.2 1.1.4 2.3.6 3.6.6.6 0 1 .4 1 1V20c0 .6-.4 1-1 1A17 17 0 0 1 3 4c0-.6.4-1 1-1h3.5c.6 0 1 .4 1 1 0 1.3.2 2.5.6 3.6.1.3 0 .7-.2 1z"/></svg>555-010-2468</span>
    <span><svg width="15" height="11" viewBox="0 0 15 11"><rect width="15" height="11" fill="#8c0d26"/><path d="M0 0l7.5 6L15 0" stroke="#262626" stroke-width="1.3" fill="none"/></svg>info@borkventures.example</span>
  </div>
  <div class="footer-nav">HOME<i>/</i>ABOUT US<i>/</i>SERVICES<i>/</i>STRATEGY<i>/</i>IT NEWS<i>/</i>CONTACT US</div>
  <div class="socials"><span></span><span></span><span></span><span></span><span></span></div>
  <div class="copyright">© Copyright-2019 Bork Ventures.All rights reserved.</div>
</footer>

</body>
</html>
```